Copperleaf Balustrade Website Redesign

I want a fresh new design for my website. Original website
www.copperleafbalustrade-example.com. Will need to add additional photos for winning designer. Please use the basic layout for new design. Looking to get a more modern, functional site to attract new customer and ne bale to highlight past projects. Need it to be easy to navigate and get in touch with me for inquiries.

Target Market(s)

Builders and home owners in WA state

Industry/Entity Type

Building, Construction, Deck building

Coding

Coded - Design and coding required

Number of Pages Required

5+ page

Font styles to use
Sans Serif

Colors
0054AA
0677BA
7BADD7
CADEEF
E8F1F8
0094D4
00A9DD
6FCCEA
C7EBF8
E9F6FB
00AB8E
00BBA5
67D7C9
C6EFE9
E9F9F6
59FF00
82FF00
B8FF75
E3FFCB
F4FFEA

Requirements
Must have
• Will need to add more photos of completed projects
Nice to have
• Fresh take on old website, something modern
Should not have
• Nothing comes to mind

```html
<!DOCTYPE html>
<html lang="en">
<head>
<meta charset="utf-8">
<title>Copperleaf Balustrade – Custom Railings</title>
<link href="https://fonts.googleapis.com/css2?family=Arimo:wght@400;700&display=swap" rel="stylesheet">
<style>
:root{
  --green:#155e2f;
  --green-dark:#0f4a24;
  --green-deep:#0b3d1d;
  --mint:#e9f5ee;
  --ink:#1c1c1c;
  --text:#333;
  --white:#fff;
  --footer:#1b1b1b;
}
*{box-sizing:border-box;margin:0;padding:0}
html,body{width:1200px;height:5106px;overflow:hidden}
body{font-family:"Arimo",Arial,sans-serif;color:var(--text);background:var(--white);position:relative}
.abs{position:absolute}
.btn{display:inline-block;background:var(--green);color:#fff;font-weight:700;font-size:13px;padding:11px 16px;text-transform:uppercase;text-decoration:none;letter-spacing:.2px}
.btn.outline{background:transparent;border:1px solid #fff}
.arrow-dot{display:inline-block;width:11px;height:11px;border-radius:50%;background:#fff;margin-left:4px;vertical-align:-1px;position:relative}
.arrow-dot::after{content:"";position:absolute;left:3px;top:3px;border-left:5px solid var(--green);border-top:2.5px solid transparent;border-bottom:2.5px solid transparent}

/* top bar */
.topbar{top:0;left:0;width:1200px;height:40px;background:var(--green)}
.topbar span{position:absolute;top:13px;color:#fff;font-size:12px;white-space:nowrap}
.brand-tab{left:516px;top:0;width:168px;height:106px;background:#fff;clip-path:polygon(14% 0,86% 0,100% 38%,100% 100%,0 100%,0 38%);display:flex;align-items:center;justify-content:center;text-align:center}
.brand-name{font-weight:700;color:var(--green);font-size:15px;line-height:1.2;text-transform:uppercase}
.nav{top:40px;left:0;width:1200px;height:70px;background:#fff;border-bottom:1px solid #e5e5e5}
.nav a{position:absolute;top:30px;font-size:14px;color:#333;text-decoration:none}
.nav a.active{color:var(--green);text-decoration:underline}
.nav .btn{top:18px;padding:11px 24px}

/* hero */
.hero{top:110px;left:0;width:1200px;height:624px}
.hero-photo{position:absolute;inset:0;background:linear-gradient(180deg,#5d6660 0%,#3b3f3c 45%,#2a2d2b 100%)}
.hero h1{position:absolute;top:215px;left:0;width:1200px;text-align:center;color:#fff;font-size:42px;line-height:54px;font-weight:700;text-transform:uppercase;letter-spacing:.5px}
.hero .btn{position:absolute;top:338px;left:530px;padding:10px 12px;font-size:12px}
.hero .ctrl{position:absolute;top:230px;width:20px;height:20px;border-radius:50%;background:#fff}
.hero svg{position:absolute;left:0;top:0}

/* welcome */
.welcome-art{left:103px;top:813px;width:472px;height:337px;background:linear-gradient(135deg,#e8efe9,#cfdcd2)}
.welcome{left:639px;top:812px;width:460px}
h2{font-size:32px;font-weight:700;color:var(--ink);text-transform:uppercase;line-height:38px}
h2 em{font-style:normal;color:var(--green)}
.welcome p{font-size:13.5px;line-height:23px;margin:16px 0 20px}

/* products */
.products{top:1235px;left:0;width:1200px;height:765px;background:var(--mint)}
.products h2{position:absolute;left:103px;top:88px}
.products .lead{position:absolute;left:104px;top:135px;font-size:14px}
.pager{position:absolute;top:98px;width:18px;height:18px;border-radius:50%;background:var(--green)}
.card{position:absolute;top:189px;width:322px;height:452px;background:#fff;border:1px solid #ddd;text-align:center;padding:6px}
.card .ph{height:210px;background:linear-gradient(160deg,#8b8b88,#555)}
.card h3{font-size:19px;color:var(--green);margin:20px 0 10px}
.card p{font-size:13.5px;line-height:22px;padding:0 22px;height:110px}
.card .btn{margin-top:12px;padding:11px 16px}
.card.featured{background:var(--green);border-color:var(--green)}
.card.featured h3,.card.featured p{color:#fff}

/* why */
.why-title{top:2074px;left:0;width:1200px;text-align:center}
.feature{position:absolute;width:450px}
.feature .icon{position:absolute;left:0;top:0;width:74px;height:74px;background:var(--green);box-shadow:6px 6px 0 #cfd9d2;display:flex;align-items:center;justify-content:center}
.feature h3{margin-left:100px;font-size:18px;color:var(--green);margin-bottom:8px}
.feature p{margin-left:100px;font-size:13.5px;line-height:22px}

/* process */
.process{top:2540px;left:0;width:1200px;height:649px;background:linear-gradient(180deg,var(--green) 0%,#13552b 100%)}
.process h2{position:absolute;left:105px;top:110px;color:#fff}
.step{position:absolute;top:376px;width:300px;text-align:center;color:#fff}
.step h3{font-size:18px;margin-bottom:12px}
.step p{font-size:13px;line-height:23px;padding:0 30px}

/* projects */
.projects-title{top:3265px;left:0;width:1200px;text-align:center}
.tabs{top:3323px;left:424px;display:flex;border:1px solid var(--green)}
.tabs span{display:block;width:175px;height:40px;line-height:40px;text-align:center;font-size:13px;font-weight:700;color:var(--green);text-transform:uppercase}
.tabs span.on{background:var(--green);color:#fff}
.slide{position:absolute;background:linear-gradient(160deg,#a8aca7,#5a5e5a)}
.slide-main{left:408px;top:3408px;width:386px;height:306px;border:6px solid #e6e6e6;background:linear-gradient(170deg,#8a8f88,#3f423f)}
.slide-main span{position:absolute;bottom:24px;left:0;width:100%;text-align:center;color:#fff;font-weight:700;font-size:17px}

/* contact */
.contact{top:3798px;left:0;width:1200px;height:426px;background:linear-gradient(180deg,#1a6a36,var(--green))}
.contact h2{position:absolute;top:85px;left:0;width:1200px;text-align:center;color:#fff}
.contact p{position:absolute;top:142px;left:120px;width:960px;text-align:center;color:#fff;font-size:18px;line-height:31px}
.contact .btn{position:absolute;top:222px;left:527px;padding:11px 18px}
.contact svg{position:absolute;left:0;top:0}

/* serving */
.serving{left:103px;top:4326px;width:420px}
.serving p{font-size:13.5px;line-height:25px;margin:18px 0 22px}
.map{left:655px;top:4268px;width:438px;height:383px;background:linear-gradient(135deg,#eef3e7,#d9ead3 55%,#e8efe1)}

/* footer */
.footer{top:4760px;left:0;width:1200px;height:287px;background:var(--footer);text-align:center}
.footer .brand-name{position:absolute;top:70px;left:0;width:1200px;color:#fff;font-size:24px;line-height:32px}
.footer nav a{position:absolute;top:218px;color:#fff;font-size:14px;text-decoration:none}
.copyright{top:5047px;left:0;width:1200px;height:59px;background:var(--green);color:#fff;text-align:center;font-size:14px;line-height:59px}
</style>
</head>
<body>

<!-- top bar -->
<div class="abs topbar">
  <span style="left:105px">
    <svg width="9" height="12" viewBox="0 0 9 12" style="vertical-align:-1px"><path d="M4.5 0a4.5 4.5 0 0 0-4.5 4.5C0 8 4.5 12 4.5 12S9 8 9 4.5A4.5 4.5 0 0 0 4.5 0z" fill="#fff"/><circle cx="4.5" cy="4.5" r="1.7" fill="#155e2f"/></svg> | 48 Fernbrook St, WA</span>
  <span style="left:245px">
    <svg width="13" height="10" viewBox="0 0 13 10" style="vertical-align:-1px"><rect width="13" height="10" fill="#fff"/><path d="M0 0l6.5 5L13 0" stroke="#155e2f" fill="none"/></svg> | info@copperleafbalustrade-example.com</span>
  <span style="left:745px;font-size:16px;top:11px">Call Us Today : +1 555 010 0199</span>
</div>

<header>
  <nav class="abs nav">
    <a class="active" style="left:103px">Home</a>
    <a style="left:197px">About Us</a>
    <a style="left:312px">Our Products</a>
    <a style="left:727px">Our Projects</a>
    <a style="left:862px">Contact Us</a>
    <a class="btn" style="left:975px;color:#fff">Log In <span class="arrow-dot"></span></a>
  </nav>
  <div class="abs brand-tab"><div class="brand-name">Copperleaf<br>Balustrade</div></div>
</header>

<!-- hero -->
<section class="abs hero">
  <div class="hero-photo" role="img" aria-label="Modern home with glass deck railings and an outdoor staircase"></div>
  <svg width="1200" height="624" viewBox="0 0 1200 624">
    <polygon points="0,455 600,580 1200,455 1200,624 0,624" fill="#fff"/>
    <polygon points="280,530 600,592 920,530 600,624" fill="#155e2f"/>
  </svg>
  <div class="ctrl" style="left:39px"></div>
  <div class="ctrl" style="left:1138px"></div>
  <h1>Durable, Stylish, and Built<br>for the Pacific Northwest</h1>
  <a class="btn">Get Started <span class="arrow-dot"></span></a>
</section>

<!-- welcome -->
<div class="abs welcome-art" role="img" aria-label="Illustration of railing panels in perspective"></div>
<section class="abs welcome">
  <h2>Welcome to<br><em>Copperleaf Balustrade</em></h2>
  <p>At Copperleaf Balustrade, we believe that every outdoor space deserves the perfect blend of style, safety, and durability. Serving homeowners, builders, and commercial developers across the Washington State, we specialize in crafting custom railing systems designed to withstand the region's unique climate while enhancing the beauty of your outdoor living spaces.</p>
  <a class="btn">Read More <span class="arrow-dot"></span></a>
</section>

<!-- products -->
<section class="abs products">
  <h2>Our <em>Products</em></h2>
  <p class="lead">We offer a wide variety of custom and railing systems designed to meet the needs of every project:</p>
  <span class="pager" style="left:1054px"></span>
  <span class="pager" style="left:1078px"></span>
  <article class="card" style="left:103px">
    <div class="ph" role="img" aria-label="Outdoor staircase with black aluminum railings"></div>
    <h3>Aluminum Railings</h3>
    <p>For a sleek, low-maintenance option, our powder-coated aluminum railings provide strength, corrosion resistance, and a modern aesthetic. Available in a range of colors and finishes.</p>
    <a class="btn">Read More <span class="arrow-dot"></span></a>
  </article>
  <article class="card featured" style="left:438px">
    <div class="ph" role="img" aria-label="Deck with tempered glass railings"></div>
    <h3>Glass Railings</h3>
    <p>Ideal for breathtaking views and clean lines, our glass railings combine tempered glass with sturdy framing to create an elegant, transparent barrier that maintains the beauty of your surroundings.</p>
    <a class="btn outline">Read More <span class="arrow-dot"></span></a>
  </article>
  <article class="card" style="left:773px">
    <div class="ph" role="img" aria-label="Indoor staircase with steel cable railing"></div>
    <h3>Cable Railings</h3>
    <p>Our stainless steel cable railing systems offer an unobstructed view, ideal for homes or businesses with scenic landscapes. The minimalist design ensures safety while preserving sightlines.</p>
    <a class="btn">Read More <span class="arrow-dot"></span></a>
  </article>
</section>

<!-- why choose -->
<h2 class="abs why-title" style="font-size:30px">Why Choose <em>Copperleaf Balustrade ?</em></h2>
<div class="feature" style="left:123px;top:2158px">
  <div class="icon"><svg width="40" height="40" viewBox="0 0 40 40" fill="none" stroke="#fff" stroke-width="2.5"><path d="M8 32L30 10M14 8l18 18M6 26l8 8"/></svg></div>
  <h3>Locally Crafted, Regionally Resilient</h3>
  <p>Our railings are designed with the Pacific Northwest's weather in mind—rain, snow, and everything in between. We use durable materials that are resistant to corrosion, moisture, and the elements, ensuring your railings stand the test of time.</p>
</div>
<div class="feature" style="left:619px;top:2158px">
  <div class="icon"><svg width="40" height="40" viewBox="0 0 40 40" fill="none" stroke="#fff" stroke-width="2.5"><path d="M8 8l24 24M32 8L8 32"/><rect x="4" y="4" width="8" height="8"/></svg></div>
  <h3>Custom Solutions for Every Need</h3>
  <p>We work closely with you to design and fabricate custom railing systems that perfectly suit your space, style, and functional requirements. From intricate designs to minimalistic finishes, we tailor every project to your vision.</p>
</div>
<div class="feature" style="left:123px;top:2326px">
  <div class="icon"><svg width="40" height="40" viewBox="0 0 40 40" fill="none" stroke="#fff" stroke-width="2.5"><path d="M8 32L32 8M8 8l24 24"/><circle cx="8" cy="8" r="4"/><circle cx="32" cy="32" r="4"/></svg></div>
  <h3>Expert Installation &amp; Craftsmanship</h3>
  <p>Our skilled craftsmen take pride in delivering exceptional workmanship, while our professional installers ensure every railing is securely mounted and aligned to meet local safety codes.</p>
</div>
<div class="feature" style="left:619px;top:2326px">
  <div class="icon"><svg width="44" height="30" viewBox="0 0 44 30" fill="none" stroke="#fff" stroke-width="2.5"><path d="M2 4h40M2 26h40M4 4v22M40 4v22M12 4v22M20 4v22M28 4v22M36 4v22"/></svg></div>
  <h3>Full-Service Partner</h3>
  <p>From the initial consultation and design process to installation and ongoing maintenance, we are with you every step of the way to ensure your project exceeds expectations.</p>
</div>

<!-- process -->
<section class="abs process">
  <h2>Our Process</h2>
  <svg class="abs" style="left:0;top:0" width="1200" height="360" viewBox="0 0 1200 360" fill="none" stroke="#fff" stroke-width="2">
    <circle cx="268" cy="276" r="88"/>
    <circle cx="599" cy="276" r="88"/>
    <circle cx="932" cy="276" r="88"/>
    <circle cx="268" cy="276" r="100" stroke-dasharray="4 5" stroke-width="1"/>
    <circle cx="599" cy="276" r="100" stroke-dasharray="4 5" stroke-width="1"/>
    <circle cx="932" cy="276" r="100" stroke-dasharray="4 5" stroke-width="1"/>
    <circle cx="354" cy="276" r="6" fill="#fff"/>
    <circle cx="688" cy="276" r="6" fill="#fff"/>
    <path d="M378 276h110M478 270l10 6-10 6M712 276h110M812 270l10 6-10 6"/>
    <path d="M228 236h60v60h-60zM238 286l40-40M248 296l48-40"/>
    <path d="M556 312h86v-70h-16v14h-14v14h-14v14h-14v14h-14v14h-14z"/>
    <path d="M904 300q28 16 56-4M918 272a14 14 0 1 0 28 0a14 14 0 1 0-28 0M932 250v-8M932 302v-8"/>
  </svg>
  <div class="step" style="left:118px"><h3>Consultation &amp; Design</h3><p>We start by listening to your vision and understanding your specific needs. Our team will offer expert advice and design ideas to help you choose the best materials and styles.</p></div>
  <div class="step" style="left:449px"><h3>Professional Installation</h3><p>Our experienced team handles all aspects of installation, from measuring to securing, ensuring your railing is safe, secure, and perfectly aligned.</p></div>
  <div class="step" style="left:782px"><h3>Ongoing Support</h3><p>We offer warranties on all of our products and services, and we are always available to help with maintenance or modifications down the road.</p></div>
</section>

<!-- projects -->
<h2 class="abs projects-title">Our <em>Projects</em></h2>
<div class="abs tabs"><span class="on">Past Projects</span><span>Current Projects</span></div>
<div class="slide" style="left:104px;top:3418px;width:304px;height:290px;clip-path:polygon(0 0,100% 10%,100% 90%,0 100%)" role="img" aria-label="Exterior stairs with horizontal metal railing"></div>
<div class="abs slide-main" role="img" aria-label="Apartment balconies with aluminum railings"><span>Aluminum Railings <span class="arrow-dot"></span></span></div>
<div class="slide" style="left:794px;top:3418px;width:304px;height:290px;clip-path:polygon(0 10%,100% 0,100% 100%,0 90%)" role="img" aria-label="Interior staircase with black metal railing"></div>

<!-- contact -->
<section class="abs contact">
  <svg width="1200" height="426" viewBox="0 0 1200 426">
    <polygon points="0,392 600,306 1200,392 1200,426 0,426" fill="#0f4a24"/>
    <polygon points="0,426 600,326 1200,426" fill="#fff"/>
  </svg>
  <h2>Get in Touch With Me for Inquiries</h2>
  <p>Ready to elevate your space with a custom railing solution that's built to last? Reach out to the Copperleaf Balustrade team for a free consultation. Let us bring your vision to life with craftsmanship, care, and precision.</p>
  <a class="btn outline">Contact Us Today</a>
</section>

<!-- serving -->
<section class="abs serving">
  <h2>Serving<br><em>Washington State</em></h2>
  <p>Copperleaf Balustrade is proud to serve the entire state of Washington. Whether you're upgrading your home's deck or outfitting a commercial space, we understand the importance of creating beautiful, durable railings that stand up to the region's diverse and often challenging weather conditions.</p>
  <a class="btn">Get a Direction</a>
</section>
<div class="abs map" role="img" aria-label="Map of central Washington State service area"></div>

<!-- footer -->
<footer class="abs footer">
  <div class="brand-name">Copperleaf<br>Balustrade</div>
  <nav>
    <a style="left:319px">Home</a>
    <a style="left:412px">About Us</a>
    <a style="left:527px">Our Products</a>
    <a style="left:668px">Our Projects</a>
    <a style="left:804px">Contact Us</a>
  </nav>
</footer>
<div class="abs copyright">© 2024 Copperleaf Balustrade | All rights reserved.</div>

</body>
</html>
```